New Business Cards for Tormin Group

We need a new Business Card to compliment our new logo. We are a vibrant design, manufacture and install business providing recreation areas, public parks and Municipal spaces. We want business cards that are classy, modern and clean.

We have recently changed our logo, and are celebrating our 40th anniversary. We want business cards with a new modern design to reflect our status.

Target Market(s)

Customers

Contact Information for Business Card

We need all the details of our 3 offices as per the business card attached. Please disregard the old logo on the business card, the other three files show our new logo.

Requirements
Must have
• All info as per attached business card but with new logo.
Nice to have

```html
<!DOCTYPE html>
<html lang="en">
<head>
<meta charset="UTF-8">
<title>Tormin Group Business Cards</title>
<link href="https://fonts.googleapis.com/css2?family=Arimo:ital,wght@0,400;0,700;1,700&display=swap" rel="stylesheet">
<style>
  :root {
    --page: #2a2b2e;
    --card: #1f2123;
    --ink: #f2f2f2;
    --muted: #d9d9d9;
    --accent: #d8262c;
    --silver: #c9c9c9;
  }
  * { box-sizing: border-box; margin: 0; padding: 0; }
  html, body { width: 1200px; height: 800px; overflow: hidden; }
  body {
    background: var(--page);
    font-family: "Arimo", Arial, sans-serif;
    position: relative;
  }
  .card {
    position: absolute;
    width: 520px;
    height: 300px;
    background: var(--card);
    border-radius: 4px;
    box-shadow: 0 10px 30px rgba(0,0,0,.45);
    overflow: hidden;
  }
  .card--front { left: 50px; top: 250px; }
  .card--back { left: 630px; top: 250px; }

  .brand {
    position: absolute;
    display: flex;
    align-items: center;
    gap: 10px;
    font-weight: 700;
    letter-spacing: 1px;
  }
  .brand__dot { border-radius: 50%; flex: none; }
  .card--front .brand { left: 50%; top: 50%; transform: translate(-50%, -50%); font-size: 34px; color: var(--silver); }
  .card--front .brand__dot { width: 60px; height: 60px; background: var(--silver); }
  .card--back .brand { right: 34px; top: 30px; font-size: 22px; color: var(--ink); }
  .card--back .brand__dot { width: 44px; height: 44px; background: var(--accent); }

  .offices { position: absolute; left: 26px; top: 26px; width: 240px; }
  .office { margin-bottom: 14px; }
  .office__title {
    font-weight: 700; font-style: italic; font-size: 13px; color: var(--ink);
    padding-bottom: 4px; border-bottom: 1px solid var(--accent); margin-bottom: 5px;
  }
  .office__line { font-size: 9.5px; line-height: 1.3; color: var(--muted); }

  .person { position: absolute; left: 292px; top: 120px; width: 200px; }
  .person__name { font-weight: 700; font-size: 15px; color: var(--ink); }
  .person__role {
    font-size: 10px; color: var(--accent); padding-bottom: 6px;
    border-bottom: 1px solid var(--accent); margin-bottom: 10px;
  }
  .contact { display: flex; align-items: center; gap: 7px; font-size: 10px; color: var(--muted); margin-bottom: 6px; }
  .contact__icon { width: 14px; height: 14px; flex: none; }
  .web { margin-top: 12px; font-weight: 700; font-size: 11px; letter-spacing: 2.5px; color: var(--ink); }
  .web__name { color: var(--accent); }
</style>
</head>
<body>
  <section class="card card--front" aria-label="Card front">
    <div class="brand"><span class="brand__dot"></span><span class="brand__name">TORMIN GROUP</span></div>
  </section>

  <section class="card card--back" aria-label="Card back">
    <div class="offices">
      <div class="office">
        <h3 class="office__title">Head Office</h3>
        <p class="office__line">P.O. Box: 48210 Abu Dhabi, U.A.E.</p>
        <p class="office__line">Tel No: +971 (0)2 5550184</p>
        <p class="office__line">Fax No: +971 (0)2 5550183</p>
        <p class="office__line">Email: sales@torminegroup.com</p>
      </div>
      <div class="office">
        <h3 class="office__title">Dubai Office</h3>
        <p class="office__line">P.O. Box: 370415 Dubai, U.A.E.</p>
        <p class="office__line">Tel No: +971 (0)4 5550691</p>
        <p class="office__line">Fax No: +971 (0)4 5550769</p>
        <p class="office__line">Email: sales@torminegroup.com</p>
      </div>
      <div class="office">
        <h3 class="office__title">Qatar Office</h3>
        <p class="office__line">P.O. Box: 17302 Doha, Qatar</p>
        <p class="office__line">Tel No: +974 55501295</p>
        <p class="office__line">Fax No: +974 55508260</p>
        <p class="office__line">Email: sales@torminegroup.com</p>
      </div>
    </div>

    <div class="brand"><span class="brand__dot"></span><span class="brand__name">TORMIN GROUP</span></div>

    <div class="person">
      <h2 class="person__name">Marcus Delane</h2>
      <p class="person__role">Managing Partner</p>
      <p class="contact">
        <svg class="contact__icon" viewBox="0 0 14 14" aria-hidden="true"><circle cx="7" cy="7" r="7" fill="#d8262c"/><rect x="4.5" y="3" width="5" height="8" rx="1" fill="#fff"/><rect x="5.5" y="4" width="3" height="5" fill="#d8262c"/></svg>
        +971 (0)50 555 0351
      </p>
      <p class="contact">
        <svg class="contact__icon" viewBox="0 0 14 14" aria-hidden="true"><circle cx="7" cy="7" r="7" fill="#d8262c"/><rect x="3.5" y="4.5" width="7" height="5" fill="#fff"/><path d="M3.5 4.5 L7 7.5 L10.5 4.5" stroke="#d8262c" stroke-width="0.9" fill="none"/></svg>
        marcus@torminegroup.com
      </p>
      <p class="web">www.<span class="web__name">torminegroup</span>.com</p>
    </div>
  </section>
</body>
</html>
```